Law Firm Web Design Project

I need a website design for my law firm. I have attached to this description the URL of a website I liked with a description of the elements of that website that appeal to me.

I am also attaching my law firm's logo, so you can review that design when you create the website design.

Reference Site: www.harborfieldcounsel-example.com

What we like about this site:
• The different layers
• Subtle designs, textures, curves
• 3 dimensional
• Floating effect
• Simple logo that stands out (we are providing logo)
• Prominent phone number
• Location of Areas of Practice
oDivorce, Legal Separation, Paternity, Spousal Maintenance, Child Custody, Child Support, Protective Orders, Community Property, Business Evaluations
• The limited amount of links across the top
o Home, Meet Our Attorney, FAQ, Contact Us
• Request A Consultation click through
• Right side bar with the moving icons
• Badges

Other Tips:
• We don’t want the website to be dark. The logo can standout and the website can have its own colors and flow.
• We would like there to be a “call to action” or way to get in touch on every page and every page view
• We would like a place for credit card icons at the bottom of the page
• Strong, yet elegant
• Finally, just use the website provided as a guide. Explore different colors, textures, shapes, shadows etc.
Updates

I would prefer the website have colors that are complementary to my logo and that are strong and elegant.  I like black, gold, amber, and tan colors.  Black should be used sparingly as an accent only, since I don't want the website to be too dark.

Please review the website I provided as an example in my project description.  I really like the three dimensional aspects of that website (web page floating on top of a background and the logo in the upper left floating on top of the web page).  I also like the use of "swirling" on the background and the webpage.  I hope this additional information is helpful.

Requirements
Must have
• I need a place to insert "client testimonials", a place to insert four logos of awards the law firm has received, a place for people to fill out a form to contact the law firm via email, and a place for people to click to review articles I have written.

```html
<!DOCTYPE html>
<html lang="en">
<head>
<meta charset="utf-8">
<title>Marlowe Law</title>
<link rel="stylesheet" href="https://fonts.googleapis.com/css2?family=Arimo:wght@400;700&family=Carlito:wght@400;700&display=swap">
<style>
:root{
  --bg:#e9e9e9;
  --bg-light:#f7f7f7;
  --ink:#2b2b2b;
  --body:#555;
  --muted:#777;
  --gold:#c9a95a;
  --gold-light:#e3cd8e;
  --gold-dark:#a5843b;
  --gold-text:#7a5a1c;
  --dark:#2e2e2e;
  --white:#fff;
  --field:#c6c6c6;
}
*{margin:0;padding:0;box-sizing:border-box}
html,body{width:819px;height:1200px;overflow:hidden}
body{position:relative;background:radial-gradient(ellipse at 25% 8%,#fff 0,var(--bg-light) 30%,var(--bg) 70%);font-family:"Arimo",Arial,sans-serif;color:var(--ink)}
.abs{position:absolute}
.swirls{position:absolute;left:0;top:0}
.brand{left:96px;top:66px;display:flex;align-items:center;gap:8px}
.brand-mark{width:40px;height:40px;background:var(--dark)}
.brand-name{font-family:"Carlito",sans-serif;font-size:25px;color:var(--gold-dark)}
.phone{left:570px;top:14px;display:flex;align-items:center;gap:10px;font-size:18px;letter-spacing:1px}
.consult{left:568px;top:56px;display:flex;align-items:center;gap:10px;font-size:13px}
.consult-dot{width:24px;height:24px;border-radius:50%;background:#c53a3a}
.nav{left:515px;top:135px;display:flex;align-items:center;font-size:11px}
.nav a{color:var(--ink);text-decoration:none;margin-right:20px}
.nav .current{background:linear-gradient(#3b3b3b,#1e1e1e);color:var(--gold-light);border-radius:3px;width:66px;height:25px;display:flex;align-items:center;justify-content:center;margin-right:9px}
.hero{left:18px;top:185px;width:780px;height:272px;background:var(--white);box-shadow:0 2px 6px rgba(0,0,0,.25)}
.hero-photo{position:absolute;left:7px;top:6px;width:766px;height:260px;background:linear-gradient(90deg,#2a2522 0,#9c7e6c 30%,#c9b1a0 50%,#3a3432 70%,#cfcbc4 90%)}
.hero-text{position:absolute;left:612px;top:101px;font-size:21px;color:#111}
.hero-arrow{width:24px;height:24px;border-radius:50%;background:#f1f1f1;box-shadow:0 1px 3px rgba(0,0,0,.35);display:flex;align-items:center;justify-content:center;font-size:10px;color:#999;top:308px}
.practice{left:22px;top:484px;width:196px;height:320px}
.practice-title{position:absolute;left:31px;top:29px;font-family:"Carlito",sans-serif;font-size:14px;color:var(--gold-light)}
.practice ul{position:absolute;left:20px;top:57px;list-style:none;font-family:"Carlito",sans-serif;font-size:10px;color:var(--ink)}
.practice li{height:19.2px;line-height:19.2px;white-space:nowrap}
.practice li::before{content:"››";display:inline-block;width:22px;font-size:9px;line-height:19.2px}
.welcome{left:246px;top:504px;width:362px}
.welcome h1{font-weight:400;font-size:15px;margin-bottom:18px}
.welcome h1 span{color:var(--gold-text)}
.welcome p{font-size:10.6px;line-height:19.4px;color:var(--body);margin-bottom:19px}
.more{font-size:9px;color:var(--ink)}
.more::after{content:"  ››"}
.testimonials{left:619px;top:494px;width:183px;height:287px;background:var(--white);border-radius:5px;box-shadow:0 1px 4px rgba(0,0,0,.25)}
.testi-title{position:absolute;left:3px;top:4px;width:177px;height:24px;border-radius:4px;background:linear-gradient(var(--gold-light),var(--gold-dark));color:var(--white);font-family:"Carlito",sans-serif;font-size:14px;padding:5px 0 0 34px}
.testi{position:absolute;left:13px;display:flex;gap:11px}
.testi-photo{width:62px;height:62px;flex:none;border:2px solid var(--white);box-shadow:0 0 2px rgba(0,0,0,.5);background:linear-gradient(#9a9488,#5d5246)}
.testi p{width:88px;font-size:8.4px;line-height:11px;color:var(--body)}
.card{background:linear-gradient(160deg,var(--gold-light),var(--gold) 50%,var(--gold-dark));border:2px solid var(--white);border-radius:5px;box-shadow:0 1px 5px rgba(0,0,0,.3);color:var(--white);font-family:"Carlito",sans-serif}
.card h2{font-weight:400;font-size:14px;color:var(--ink)}
.card .small{font-size:10px;font-weight:700}
.card-call{left:26px;top:827px;width:196px;height:136px}
.awards{left:239px;top:826px;width:354px;height:139px;background:var(--white);border-radius:3px}
.awards h2{position:absolute;left:41px;top:11px;font-family:"Carlito",sans-serif;font-weight:400;font-size:14px}
.badge{position:absolute;background:#e4e4e4;border:1px solid #555}
.card-side{left:618px;top:828px;width:186px;height:140px}
.icon-box{position:absolute;width:24px;height:36px;background:#333;border-radius:3px}
.contact-title{font-family:"Carlito",sans-serif;font-weight:400;font-size:14px;left:67px;top:1034px}
.field{width:142px;height:23px;background:var(--field);border-radius:3px;font-size:9px;color:var(--ink);padding:6px 0 0 18px}
.submit{left:306px;top:1121px;width:57px;height:21px;border-radius:3px;background:linear-gradient(var(--gold-light),var(--gold-dark));font-size:9px;font-weight:700;display:flex;align-items:center;justify-content:center}
.pay{top:1040px;width:27px;height:17px;border:1px solid #999;border-radius:2px}
.legal{left:538px;top:1108px;font-size:9px}
.copy{left:567px;top:1136px;font-size:9px}
.social{top:1170px;width:18px;height:18px;border-radius:2px}
</style>
</head>
<body>
<svg class="swirls" width="819" height="1200" aria-hidden="true">
  <path d="M0 140 C200 200 420 150 560 115 C680 85 760 95 819 110 L819 175 L0 175Z" fill="#d4d4d4"/>
  <path d="M0 150 C210 205 430 160 570 125 C690 95 760 100 819 118" fill="none" stroke="#fff" stroke-width="4"/>
  <path d="M0 170 C200 190 400 175 819 172" fill="none" stroke="#bcbcbc" stroke-width="2"/>
  <path d="M0 1035 C150 1000 320 1000 480 1045 C620 1085 740 1080 819 1050 L819 1200 L0 1200Z" fill="#dedede"/>
  <path d="M0 1030 C150 995 320 995 480 1040 C620 1080 740 1075 819 1045" fill="none" stroke="#fff" stroke-width="3"/>
</svg>

<div class="abs brand"><span class="brand-mark"></span><span class="brand-name">Marlowe Law</span></div>
<div class="abs phone">
  <svg width="20" height="20" viewBox="0 0 20 20" aria-hidden="true"><rect width="20" height="20" rx="4" fill="#6b5a34"/><path d="M6 4c1 0 2 3 1.5 3.8L6.5 9c1 2 2.5 3.5 4.5 4.5l1.2-1c.8-.5 3.8.5 3.8 1.5 0 1.5-1.5 2.5-3 2.5C8 16.5 3.5 12 3.5 7 3.5 5.5 4.5 4 6 4z" fill="#f0e2b5"/></svg>
  <span>555 214 0187</span>
</div>
<div class="abs consult"><span class="consult-dot"></span><span>Request A Consultation</span></div>
<nav class="abs nav"><a class="current" href="#">Home</a><a href="#">Meet Our Attorney</a><a href="#">FAQ</a><a href="#">Contact Us</a></nav>

<section class="abs hero">
  <div class="hero-photo" role="img" aria-label="Close-up of a couple's joined hands during a wedding ceremony"></div>
  <div class="hero-text">PROBLEMS?</div>
</section>
<div class="abs hero-arrow" style="left:13px">◀</div>
<div class="abs hero-arrow" style="left:783px">▶</div>

<aside class="abs practice">
  <svg width="196" height="320" aria-hidden="true">
    <path d="M4 10 C60 -2 120 14 192 4 L192 302 C130 290 70 312 4 300Z" fill="#fff" stroke="#ccc" filter="drop-shadow(0 1px 2px rgba(0,0,0,.3))"/>
    <path d="M4 10 C60 -2 120 14 192 4 L192 50 L4 50Z" fill="#2e2e2e"/>
  </svg>
  <div class="practice-title">Areas of Practice</div>
  <ul>
    <li>Family Law</li><li>Divorce</li><li>Alimony</li><li>Child Custody</li><li>Child Support</li><li>Collaborative Divorce</li><li>Contested Divorce</li><li>Division of Assets</li><li>Family/Relative Adoption</li><li>Fathers’ Rights</li><li>Grandparents’ Rights</li><li>Guardianship</li><li>Legal Separation</li>
  </ul>
</aside>

<main class="abs welcome">
  <h1>WELCOME TO <span>MARLOWE LAW</span></h1>
  <p>Nunc varius facilisis eros. Sed erat. In in velit quis arcu ornare laoreet. Curabitur adipiscing luctus massa.Integer ut purus ac augue commodo commodo. Nunc nec mi eu justo tempor consectetuer. Etiam vitae nisl. In dignissim lacus ut ante. Cras elit lectus, bibendum a, adipiscing vitae, commodo et, dui.</p>
  <p>Lorem ipsum dolor sit amet, consectetuer adipiscing elit. Nam nibh. Nunc varius facilisis eros. Sed erat. In in velit quis arcu ornare laoreet. Curabitur adipiscing luctus massa.Lorem ipsum dolor sit amet, consectetuer adipiscing elit. Nam nibh. Nunc varius facilisis eros. Sed erat. In in velit quis arcu ornare laoreet. Curabitur adipiscing luctus massa.</p>
  <div class="more" style="margin-left:284px;margin-top:-6px">Read More</div>
</main>

<aside class="abs testimonials">
  <div class="testi-title">Testimonials</div>
  <div class="testi" style="top:38px"><div class="testi-photo" role="img" aria-label="Client portrait"></div><p>Nunc varius facilisis eros. Sed erat. In in velit quis arcu ornare laoreet. luctus massa.</p></div>
  <div class="testi" style="top:117px;left:16px"><div class="testi-photo" role="img" aria-label="Client portrait"></div><p>Nunc varius facilisis eros. Sed erat. In in velit quis arcu ornare laoreet. luctus massa.</p></div>
  <div class="testi" style="top:196px;left:16px"><div class="testi-photo" role="img" aria-label="Client portrait with umbrella"></div><p>Nunc varius facilisis eros. Sed erat. In in velit quis arcu ornare laoreet. luctus massa.</p></div>
  <div class="more" style="position:absolute;left:116px;top:268px">Read More</div>
</aside>

<section class="abs card card-call">
  <h2 style="position:absolute;left:20px;top:9px">Click to Call</h2>
  <div class="icon-box" style="left:18px;top:52px"></div>
  <p class="small" style="position:absolute;left:58px;top:51px;width:130px;line-height:14px">Have a question about your case? Click here to connect to our office</p>
  <p class="small" style="position:absolute;left:122px;top:110px">Click Here &nbsp;›</p>
</section>

<section class="abs awards">
  <h2>Awards</h2>
  <div class="badge" style="left:17px;top:46px;width:113px;height:74px"></div>
  <div class="badge" style="left:152px;top:46px;width:113px;height:74px"></div>
  <div class="badge" style="left:272px;top:18px;width:67px;height:108px;border-radius:4px"></div>
</section>

<section class="abs card card-side">
  <div class="icon-box" style="left:20px;top:11px"></div>
  <h2 style="position:absolute;left:64px;top:13px">Video Center</h2>
  <p class="small" style="position:absolute;left:66px;top:33px">Need More Information</p>
  <p class="small" style="position:absolute;left:119px;top:49px">Click Here &nbsp;›</p>
  <div class="icon-box" style="left:20px;top:75px;background:#eee;border:1px solid #333"></div>
  <h2 style="position:absolute;left:62px;top:78px">Case Evaluation</h2>
  <p class="small" style="position:absolute;left:66px;top:98px">Fill Out Online</p>
  <p class="small" style="position:absolute;left:100px;top:114px">Click Here &nbsp;›</p>
</section>

<section class="contact">
  <h2 class="abs contact-title">Contact</h2>
  <div class="abs field" style="left:68px;top:1064px">Name</div>
  <div class="abs field" style="left:68px;top:1097px">Phone</div>
  <div class="abs field" style="left:68px;top:1130px">Email</div>
  <div class="abs field" style="left:222px;top:1062px;height:49px;padding-top:10px;padding-left:21px">Message</div>
  <div class="abs submit">SUBMIT</div>
</section>

<div class="abs pay" style="left:592px;background:#e8e8ef"></div>
<div class="abs pay" style="left:627px;background:#f1e4d8"></div>
<div class="abs pay" style="left:663px;background:#dbe6f0"></div>
<div class="abs pay" style="left:698px;background:#f1ebe1"></div>

<div class="abs legal">Privacy Policy &nbsp;| &nbsp;Contact Us &nbsp;| &nbsp;Resources &nbsp;| &nbsp;Site Map</div>
<div class="abs copy">© 2012 Marlowelaw, All Rights Reserved</div>

<div class="abs social" style="left:596px;background:#4a5f8f"></div>
<div class="abs social" style="left:628px;background:#6ab9e0"></div>
<div class="abs social" style="left:660px;background:#e48a3a"></div>
<div class="abs social" style="left:692px;background:#3a72a8"></div>
<div class="abs social" style="left:724px;background:#c9c9c9"></div>
</body>
</html>
```